Restyle corporate identity (+ logo) for a road construction company

We need a new logo and stationary design for our company VARNOK path. VARNOK path® increases the road base strength, while reducing major costs and time of road construction. Attached some examples of the current design.

Our wishes for the new logo:
- Business look
- Style sheet
- Modern

More information: www.varnokpath.example
Updates

Target Market(s)

Government

Industry/Entity Type

Construction

Requirements
Must have
• Logo (with road sign) + text

```html
<!DOCTYPE html>
<html lang="en">
<head>
<meta charset="utf-8">
<title>VARNOK path – Business Card</title>
<link rel="stylesheet" href="https://fonts.googleapis.com/css2?family=Open+Sans:wght@400;600&display=swap">
<style>
  :root {
    --backdrop: #e4e5e7;
    --card-white: #f4f4f5;
    --brand-blue: #1479de;
    --text-dark: #3a3b3d;
    --text-muted: #8a8b8e;
    --divider: #b9babc;
    --on-blue: #e6eef8;
  }
  * { box-sizing: border-box; margin: 0; padding: 0; }
  html, body {
    width: 1105px;
    height: 1200px;
    overflow: hidden;
    background: var(--backdrop);
    font-family: "Open Sans", Arial, sans-serif;
  }
  .canvas { position: relative; width: 1105px; height: 1200px; }
  .card {
    position: absolute;
    left: 182px;
    width: 746px;
    height: 425px;
  }
  .card-front { top: 119px; background: var(--card-white); }
  .card-back { top: 636px; background: var(--brand-blue); }

  .brand-lockup {
    position: absolute;
    left: 80px;
    top: 190px;
    display: flex;
    align-items: center;
    gap: 14px;
  }
  .brand-square {
    width: 40px;
    height: 40px;
    background: var(--brand-blue);
  }
  .brand-name {
    font-weight: 600;
    font-size: 34px;
    color: var(--brand-blue);
    letter-spacing: 0.5px;
    white-space: nowrap;
  }

  .divider {
    position: absolute;
    left: 395px;
    top: 88px;
    width: 1px;
    height: 263px;
    background: var(--divider);
  }

  .contact { position: absolute; left: 427px; top: 86px; }
  .person-name {
    font-weight: 600;
    font-size: 26px;
    color: var(--brand-blue);
    line-height: 34px;
  }
  .person-title {
    font-size: 20px;
    color: var(--text-muted);
    line-height: 26px;
  }
  .address {
    margin-top: 20px;
    font-size: 19px;
    color: var(--text-dark);
    line-height: 27px;
    font-style: normal;
  }
  .contact-list { margin-top: 10px; list-style: none; }
  .contact-list li {
    display: flex;
    align-items: center;
    gap: 10px;
    font-size: 19px;
    color: var(--text-dark);
    line-height: 29px;
  }
  .contact-icon { width: 17px; height: 17px; flex: none; }

  .back-brand {
    position: absolute;
    left: 0;
    right: 0;
    top: 185px;
    text-align: center;
    font-weight: 600;
    font-size: 46px;
    color: var(--on-blue);
    letter-spacing: 1px;
  }
  .back-url {
    position: absolute;
    left: 0;
    right: 0;
    top: 357px;
    text-align: center;
    font-size: 18px;
    color: var(--on-blue);
    letter-spacing: 7px;
  }
</style>
</head>
<body>
<main class="canvas">
  <section class="card card-front" aria-label="Business card front">
    <div class="brand-lockup">
      <span class="brand-square" aria-hidden="true"></span>
      <span class="brand-name">VARNOK path</span>
    </div>

    <span class="divider" aria-hidden="true"></span>

    <div class="contact">
      <p class="person-name">Elsa Marwick</p>
      <p class="person-title">CEO/Founder</p>
      <address class="address">
        Lindenkade 58<br>
        3012 KL Riverstad<br>
        The Netherlands
      </address>
      <ul class="contact-list">
        <li>
          <svg class="contact-icon" viewBox="0 0 24 24" aria-hidden="true">
            <path fill="#1479de" d="M6.6 10.8a15.1 15.1 0 0 0 6.6 6.6l2.2-2.2c.3-.3.7-.4 1-.2 1.1.4 2.3.6 3.6.6.6 0 1 .4 1 1V20c0 .6-.4 1-1 1A17 17 0 0 1 3 4c0-.6.4-1 1-1h3.5c.6 0 1 .4 1 1 0 1.3.2 2.5.6 3.6.1.3 0 .7-.2 1z"/>
          </svg>
          612 480 3915
        </li>
        <li>
          <svg class="contact-icon" viewBox="0 0 24 24" aria-hidden="true">
            <rect x="2" y="5" width="20" height="14" rx="1.5" fill="#1479de"/>
            <path d="M3 6.5l9 6.5 9-6.5" fill="none" stroke="#f4f4f5" stroke-width="1.6"/>
          </svg>
          info@varnokpath.example
        </li>
        <li>
          <svg class="contact-icon" viewBox="0 0 24 24" aria-hidden="true">
            <circle cx="12" cy="12" r="10" fill="#1479de"/>
            <path d="M2 12h20M12 2c3 3 3 17 0 20M12 2c-3 3-3 17 0 20" fill="none" stroke="#f4f4f5" stroke-width="1.4"/>
          </svg>
          www.varnokpath.example
        </li>
      </ul>
    </div>
  </section>

  <section class="card card-back" aria-label="Business card back">
    <p class="back-brand">VARNOK path</p>
    <p class="back-url">www.varnokpath.example</p>
  </section>
</main>
</body>
</html>
```